Irrigation Business needs their business cards modernised and revamped

I would like to keep my current logo, colours and revamp the format of the card.

I would like the card to be clean yet important.

Im not sure if you include texture but i would like the named logo to be indented into the card etc.

show me something alive and free something thats clinical to the point yet has a feel of achievement. i would like people to go nice card.

Target Market(s)

high end clients, corporate, sports field manger, the guys that make the decisions

Industry/Entity Type

Business

Contact Information for Business Card

nformation to be included

Dean Harlow (Director)
0487305526
dean@kolvat.biz
www.kestonfieldworks.com

instagram logo
google logo
facebook logo

Colors

Designer to choose colors to be used in the design.

Requirements
Nice to have
• indentations a really nice feel to the card good texture

```html
<!DOCTYPE html>
<html lang="en">
<head>
<meta charset="utf-8">
<title>Keston Fieldworks – Business Card</title>
<link href="https://fonts.googleapis.com/css2?family=Roboto:wght@400;700&family=Roboto+Condensed:wght@500&display=swap" rel="stylesheet">
<style>
  :root {
    --backdrop: #2b2b2b;
    --card-white: #f3f3f3;
    --brand-blue: #3a6ca8;
    --brand-navy: #2d5fa4;
    --brand-green: #3aa867;
    --ink-light: #ffffff;
    --rule-soft: rgba(255,255,255,0.45);
  }
  * { box-sizing: border-box; margin: 0; padding: 0; }
  html, body { width: 1200px; height: 960px; overflow: hidden; }
  body { background: var(--backdrop); position: relative; font-family: "Roboto", Arial, sans-serif; }

  .card {
    position: absolute;
    width: 600px;
    height: 343px;
    overflow: hidden;
    box-shadow: 2px 3px 6px rgba(0,0,0,0.55);
  }
  .card-front { left: 314px; top: 113px; background: var(--card-white); }
  .card-back  { left: 311px; top: 472px; background: var(--brand-blue); }

  .front-wave { position: absolute; left: 0; top: 0; width: 600px; height: 343px; }

  .brand-mark {
    position: absolute; left: 50%; transform: translateX(-50%);
    border-radius: 50%;
  }
  .card-front .brand-mark { top: 44px; width: 98px; height: 98px; background: var(--brand-navy); }
  .card-back .brand-mark  { top: 80px; width: 108px; height: 108px; border: 3px solid var(--ink-light); }

  .brand-name {
    position: absolute; left: 0; width: 100%;
    text-align: center; font-weight: 700; font-size: 33px; letter-spacing: -0.5px;
    line-height: 1;
  }
  .card-front .brand-name { top: 153px; color: var(--brand-navy); }
  .card-back .brand-name  { top: 198px; color: var(--ink-light); }

  .holder {
    position: absolute; top: 277px; left: 0; width: 100%;
    text-align: center; color: var(--ink-light);
  }
  .holder-name { font-family: "Roboto Condensed", Arial, sans-serif; font-weight: 500; font-size: 21px; }
  .holder-role { font-size: 15px; margin-left: 6px; letter-spacing: 0.3px; }

  .contact-line {
    position: absolute; top: 304px; left: 0; width: 100%;
    display: flex; justify-content: center; gap: 9px;
    color: var(--ink-light); font-size: 14px;
  }
  .contact-item { display: flex; align-items: center; gap: 6px; }
  .contact-item svg { width: 13px; height: 13px; fill: var(--ink-light); }

  .social-row {
    position: absolute; top: 291px; left: 0; width: 100%; height: 28px;
    display: flex; justify-content: center; align-items: center; gap: 3px;
  }
  .social-rule { width: 210px; height: 1px; background: linear-gradient(to right, transparent, var(--rule-soft)); }
  .social-rule.right { background: linear-gradient(to left, transparent, var(--rule-soft)); }
  .social-dot { width: 28px; height: 28px; border-radius: 50%; background: var(--ink-light); }
</style>
</head>
<body>

<section class="card card-front">
  <svg class="front-wave" viewBox="0 0 600 343" aria-hidden="true">
    <path d="M0 203 Q300 310 600 203 L600 343 L0 343 Z" fill="var(--brand-blue)"/>
    <path d="M0 199 Q300 306 600 199" fill="none" stroke="var(--brand-green)" stroke-width="5"/>
    <path d="M0 203.5 Q300 310.5 600 203.5" fill="none" stroke="#ffffff" stroke-width="1.5"/>
  </svg>
  <div class="brand-mark"></div>
  <div class="brand-name">KESTON FIELDWORKS</div>
  <div class="holder">
    <span class="holder-name">DEAN HARLOW&nbsp; -</span><span class="holder-role">DIRECTOR</span>
  </div>
  <div class="contact-line">
    <span class="contact-item">
      <svg viewBox="0 0 24 24"><path d="M6.6 10.8a15 15 0 0 0 6.6 6.6l2.2-2.2c.3-.3.7-.4 1-.2 1.1.4 2.3.6 3.6.6.6 0 1 .4 1 1V20c0 .6-.4 1-1 1A17 17 0 0 1 3 4c0-.6.4-1 1-1h3.5c.6 0 1 .4 1 1 0 1.3.2 2.5.6 3.6.1.3 0 .7-.2 1z"/></svg>
      0487305526
    </span>
    <span class="contact-item">
      <svg viewBox="0 0 24 24"><path d="M2 5h20v14H2z M3.5 6.5 12 13l8.5-6.5" fill="none" stroke="#fff" stroke-width="2.5"/></svg>
      dean@kolvat.biz
    </span>
    <span class="contact-item">
      <svg viewBox="0 0 24 24"><circle cx="12" cy="12" r="9.5" fill="none" stroke="#fff" stroke-width="2.5"/><path d="M2.5 12h19M12 2.5c3 3 3 16 0 19M12 2.5c-3 3-3 16 0 19" fill="none" stroke="#fff" stroke-width="2"/></svg>
      kestonfieldworks.com
    </span>
  </div>
</section>

<section class="card card-back">
  <div class="brand-mark"></div>
  <div class="brand-name">KESTON FIELDWORKS</div>
  <div class="social-row">
    <span class="social-rule"></span>
    <span class="social-dot" role="img" aria-label="Social profile"></span>
    <span class="social-dot" role="img" aria-label="Social profile"></span>
    <span class="social-dot" role="img" aria-label="Social profile"></span>
    <span class="social-rule right"></span>
  </div>
</section>

</body>
</html>
```